Medical Practice needs a Letterhead Design

We need a clean, modern letterhead design for our stem cell medical practice.

Industry/Entity Type

Medical

```html
<!DOCTYPE html>
<html lang="en">
<head>
<meta charset="UTF-8">
<title>Verana Medical Letterhead</title>
<link rel="stylesheet" href="https://fonts.googleapis.com/css2?family=Crimson+Text:wght@400&display=swap">
<style>
  :root {
    --navy: #0b3347;
    --lime: #b2c63c;
    --paper: #ffffff;
    --ink: #111111;
  }
  * { margin: 0; padding: 0; box-sizing: border-box; }
  html, body {
    width: 927px;
    height: 1200px;
    overflow: hidden;
    background: var(--paper);
  }
  .letterhead {
    position: relative;
    width: 927px;
    height: 1200px;
    background: var(--paper);
    font-family: "Crimson Text", Georgia, serif;
    color: var(--ink);
    overflow: hidden;
  }
  .header-wave {
    position: absolute;
    top: 0;
    left: 0;
    width: 927px;
    height: 180px;
    display: block;
  }
  .brand {
    position: absolute;
    top: 218px;
    left: 126px;
    display: flex;
    align-items: center;
    gap: 12px;
  }
  .brand-dot {
    width: 14px;
    height: 14px;
    border-radius: 50%;
    background: var(--lime);
  }
  .brand-name {
    font-family: "Crimson Text", Georgia, serif;
    font-weight: 400;
    font-size: 44px;
    line-height: 1;
    color: var(--navy);
  }
  .contact-line {
    position: absolute;
    left: 0;
    top: 1134px;
    width: 927px;
    padding: 0 50px;
    display: flex;
    justify-content: space-between;
    align-items: center;
    font-size: 17.5px;
    letter-spacing: 0.2px;
  }
  .contact-sep {
    width: 5px;
    height: 5px;
    border-radius: 50%;
    background: var(--ink);
  }
  .footer-band {
    position: absolute;
    left: 0;
    bottom: 0;
    width: 927px;
    height: 35px;
    background: var(--navy);
  }
</style>
</head>
<body>
  <div class="letterhead">
    <svg class="header-wave" viewBox="0 0 927 180" aria-hidden="true">
      <path fill="var(--lime)" d="M0 0 H927 V169 C800 164 640 118 458 76 C300 44 100 46 0 104 Z"/>
      <path fill="var(--navy)" d="M0 0 H927 V147 C800 142 640 96 458 55 C300 26 100 28 0 82 Z"/>
    </svg>

    <div class="brand">
      <span class="brand-dot"></span>
      <span class="brand-name">Verana Medical</span>
    </div>

    <div class="contact-line">
      <span class="contact-item">Address</span>
      <span class="contact-sep"></span>
      <span class="contact-item">Phone Number</span>
      <span class="contact-sep"></span>
      <span class="contact-item">Fax Number</span>
      <span class="contact-sep"></span>
      <span class="contact-item">Website</span>
    </div>

    <div class="footer-band"></div>
  </div>
</body>
</html>
```